Business card for my new company (Accounting firm)

I need a business card for my new business Brightwell Advisory and Ledger SA. Our services are accounting, tax, audit and financial management. Our customers are small companies, start-ups and new companies. The final design has to show financial security, trust and growth. Please find our logo attached to the business card. Text for the business card: Brightwell Advisory and Ledger SA Tomas Varenholt Director and Founder Certified Accountant Tel. 022 418 57 34 tv@clairevalconseil.ch www.clairevalconseil.ch Rue des Vergières 27 1201 Geneva
Target Market(s)
Our customers are small companies, start-ups and new companies.
Industry/Entity Type
Finance And Accounting
Contact Information for Business Card
Claireval Conseil et Comptes SA
Tomas Varenholt
Directeur et Fondateur
Expert-comptable diplômé
Tél. 022 418 57 34
tv@clairevalconseil.ch
www.clairevalconseil.ch
Rue des Vergières 27
1201 Genève

```html
<!DOCTYPE html>
<html lang="fr">
<head>
<meta charset="utf-8">
<title>Claireval Conseil et Comptes SA – Carte de visite</title>
<link rel="stylesheet" href="https://fonts.googleapis.com/css2?family=Montserrat:wght@400;500;600&family=Roboto:wght@400&display=swap">
<style>
  :root {
    --bg: #2a2a2c;
    --brand-blue: #1a6496;
    --brand-sky: #2ea8e0;
    --ink: #3a3a3c;
    --rule: #8a8a8a;
    --paper: #ffffff;
  }
  * { margin: 0; padding: 0; box-sizing: border-box; }
  html, body { width: 1200px; height: 960px; overflow: hidden; background: var(--bg); }
  body { position: relative; font-family: "Montserrat", sans-serif; }

  .card {
    position: absolute;
    width: 560px;
    height: 340px;
    left: 320px;
    overflow: hidden;
    box-shadow: 0 10px 30px rgba(0,0,0,.45);
  }

  /* Back side */
  .card--back { top: 90px; background: var(--brand-blue); }
  .back-brand {
    position: absolute; left: 0; right: 0; top: 118px;
    display: flex; justify-content: center; align-items: center; gap: 14px;
  }
  .back-brand__mark { width: 26px; height: 26px; background: var(--paper); }
  .back-brand__name {
    color: var(--paper); font-weight: 600; font-size: 44px; letter-spacing: 3px;
  }
  .back-web {
    position: absolute; left: 0; right: 0; top: 250px; text-align: center;
    color: var(--paper); font-family: "Roboto", sans-serif; font-size: 15px; letter-spacing: 4px;
  }

  /* Front side */
  .card--front { top: 530px; background: var(--paper); }
  .front-swoosh { position: absolute; left: 0; top: 0; width: 560px; height: 340px; }
  .front-brand {
    position: absolute; left: 34px; top: 132px; width: 220px;
    display: flex; align-items: center; gap: 10px;
  }
  .front-brand__mark { width: 18px; height: 18px; background: var(--brand-blue); flex: none; }
  .front-brand__name { color: var(--ink); font-weight: 600; font-size: 30px; letter-spacing: 1px; }
  .front-rule {
    position: absolute; left: 262px; top: 34px; width: 1px; height: 180px; background: var(--rule);
  }
  .contact { position: absolute; left: 284px; top: 30px; color: var(--ink); }
  .contact__name { color: var(--brand-sky); font-weight: 600; font-size: 21px; margin-bottom: 4px; }
  .contact__role { font-weight: 600; font-size: 13px; line-height: 17px; }
  .contact__address { font-weight: 500; font-size: 12.5px; line-height: 17px; margin-top: 12px; }
  .contact__list { list-style: none; margin-top: 12px; font-weight: 500; font-size: 12.5px; line-height: 18px; }
  .contact__list li { display: flex; align-items: center; gap: 7px; }
  .contact__list svg { width: 11px; height: 11px; fill: var(--brand-sky); flex: none; }
</style>
</head>
<body>

  <section class="card card--back" aria-label="Verso de la carte">
    <div class="back-brand">
      <span class="back-brand__mark"></span>
      <span class="back-brand__name">CLAIREVAL</span>
    </div>
    <p class="back-web">www.clairevalconseil.ch</p>
  </section>

  <section class="card card--front" aria-label="Recto de la carte">
    <svg class="front-swoosh" viewBox="0 0 560 340" aria-hidden="true">
      <path d="M0 309 C 200 304, 420 276, 560 215 L560 340 L0 340 Z" fill="var(--brand-blue)"/>
      <path d="M0 300 C 200 295, 420 264, 560 200 L560 208 C 420 271, 200 301, 0 305 Z" fill="var(--brand-sky)"/>
    </svg>

    <div class="front-brand">
      <span class="front-brand__mark"></span>
      <span class="front-brand__name">CLAIREVAL</span>
    </div>

    <div class="front-rule"></div>

    <div class="contact">
      <p class="contact__name">Tomas Varenholt</p>
      <p class="contact__role">Directeur et Fondateur<br>Expert-comptable diplômé</p>
      <p class="contact__address">Rue des Vergières 27<br>1201 Genève</p>
      <ul class="contact__list">
        <li><svg viewBox="0 0 24 24"><path d="M6.6 10.8a15 15 0 0 0 6.6 6.6l2.2-2.2a1 1 0 0 1 1-.25 11.4 11.4 0 0 0 3.6.57 1 1 0 0 1 1 1V20a1 1 0 0 1-1 1A17 17 0 0 1 3 4a1 1 0 0 1 1-1h3.5a1 1 0 0 1 1 1c0 1.25.2 2.45.57 3.57a1 1 0 0 1-.25 1z"/></svg>022 418 57 34</li>
        <li><svg viewBox="0 0 24 24"><path d="M2 5h20v14H2z M2 5l10 8 10-8"/></svg>tv@clairevalconseil.ch</li>
        <li><svg viewBox="0 0 24 24"><circle cx="12" cy="12" r="10"/></svg>www.clairevalconseil.ch</li>
      </ul>
    </div>
  </section>

</body>
</html>
```